Rultan Staffing Full Length Retractable Office Banner

I need a design for a full-length retractable banner and A-Frame Sign for each of my offices. I have included designs that have been incorporated into a poster and tri-fold as a sample. I would like to see a colorful eyecatching banner that focuses on people. Would like to see some diversity with men and woman and different races.
Rultan Staffing is a light industrial staffing firm. www.RultanStaffing.example

Target Market(s)

Job seekers looking for employment

Industry/Entity Type

Staffing / Recruiting

Font styles to use
Other font styles liked:
• Professional yet fun

Requirements
Must have
• Eye catching design with young hip vibe.
Nice to have
• primary colors with light industrial type jobs

```html
<!DOCTYPE html>
<html lang="en">
<head>
<meta charset="utf-8">
<title>Rultan Staffing Retractable Banner</title>
<link rel="stylesheet" href="https://fonts.googleapis.com/css2?family=Oswald:wght@400;600;700&family=Roboto+Condensed:wght@400;700&family=Montserrat:wght@500&display=swap">
<style>
  :root {
    --backdrop: #e9e9ea;
    --banner: #ffffff;
    --navy: #2b2a63;
    --red: #e3262b;
    --green: #1d6b33;
    --yellow: #f0cc1a;
    --grey: #8a8a8a;
  }
  * { margin: 0; padding: 0; box-sizing: border-box; }
  html, body { width: 1200px; height: 930px; overflow: hidden; background: var(--backdrop); }
  .banner {
    position: absolute; left: 410px; top: 20px;
    width: 380px; height: 890px;
    background: var(--banner);
    box-shadow: 0 2px 10px rgba(0,0,0,.12);
  }
  .brand-name {
    position: absolute; top: 70px; left: 0; width: 100%;
    text-align: center;
    font-family: "Oswald", sans-serif; font-weight: 600;
    font-size: 54px; line-height: 1.05; color: var(--navy);
  }
  .people-ring {
    position: absolute; left: 34px; top: 217px;
    width: 312px; height: 312px;
  }
  .ring-name {
    position: absolute; left: 0; top: 138px; width: 312px;
    text-align: center;
    font-family: "Oswald", sans-serif; font-weight: 600;
    font-size: 24px; color: var(--navy);
  }
  .headline {
    position: absolute; top: 578px; left: 0; width: 100%;
    text-align: center;
  }
  .headline .connecting {
    font-family: "Oswald", sans-serif; font-weight: 700;
    font-size: 58px; line-height: 62px; color: var(--navy);
    letter-spacing: 0.5px;
  }
  .headline .people {
    font-family: "Roboto Condensed", sans-serif;
    font-size: 42px; line-height: 44px; color: var(--red);
  }
  .headline .people strong { font-weight: 700; }
  .headline .with {
    font-family: "Roboto Condensed", sans-serif;
    font-size: 25px; line-height: 28px; color: var(--navy);
  }
  .headline .organizations {
    font-family: "Oswald", sans-serif; font-weight: 600;
    font-size: 35px; line-height: 40px; color: var(--green);
  }
  .color-bar {
    position: absolute; top: 804px; left: 0; width: 100%; height: 6px;
    display: flex; gap: 2px;
  }
  .color-bar span { flex: 1; }
  .color-bar .red { background: var(--red); }
  .color-bar .green { background: var(--green); }
  .color-bar .yellow { background: var(--yellow); }
  .color-bar .navy { background: var(--navy); }
  .web-address {
    position: absolute; top: 840px; left: 0; width: 100%;
    text-align: center;
    font-family: "Montserrat", sans-serif; font-weight: 500;
    font-size: 15px; letter-spacing: 4px; color: var(--navy);
  }
  .web-address .domain { color: var(--red); }
</style>
</head>
<body>
  <div class="banner">
    <div class="brand-name">Rultan<br>Staffing</div>

    <div class="people-ring">
      <svg width="312" height="312" viewBox="0 0 312 312" role="img" aria-label="Photo of a diverse group of people seen from above, standing in a circle">
        <defs>
          <linearGradient id="ringTone" x1="0" y1="0" x2="1" y2="1">
            <stop offset="0" stop-color="#e85a4f"/>
            <stop offset="0.35" stop-color="#3c5fa8"/>
            <stop offset="0.65" stop-color="#6aa84f"/>
            <stop offset="1" stop-color="#e2c13a"/>
          </linearGradient>
        </defs>
        <circle cx="156" cy="156" r="130" fill="none" stroke="url(#ringTone)" stroke-width="50" opacity="0.75"/>
      </svg>
      <div class="ring-name">Rultan Staffing</div>
    </div>

    <div class="headline">
      <div class="connecting">CONNECTING</div>
      <div class="people"><strong>GREAT</strong> PEOPLE</div>
      <div class="with">WITH</div>
      <div class="organizations">GREAT ORGANIZATIONS!</div>
    </div>

    <div class="color-bar">
      <span class="red"></span><span class="green"></span><span class="yellow"></span><span class="navy"></span>
    </div>

    <div class="web-address">www.<span class="domain">RultanStaffing</span>.example</div>
  </div>
</body>
</html>
```